Heron Loan Partners Business Card

We need a business card design for our mortgage servicing company. In addition to servicing the loans of homeowners, we help homeowners with purchasing their homes and any mortgage refinancing. We would like to see designs that use the colors in the logo attached below (gold-ish yellow and navy blue), and any other design you deem fit! The design should communicate a simpler life with smart mortgages provided by Heron.

```html
<!DOCTYPE html>
<html lang="en">
<head>
<meta charset="utf-8">
<title>Heron Loan Partners – Business Card</title>
<link rel="stylesheet" href="https://fonts.googleapis.com/css2?family=Figtree:wght@400;700&display=swap">
<style>
  :root {
    --backdrop: #464646;
    --paper: #ffffff;
    --gold: #e0b33e;
    --navy: #262256;
    --ink: #141414;
  }
  * { box-sizing: border-box; margin: 0; padding: 0; }
  html, body {
    width: 1200px; height: 1200px; overflow: hidden;
    background: var(--backdrop);
    font-family: "Figtree", sans-serif;
  }
  .card {
    position: absolute; left: 193px; width: 818px; height: 463px;
    border-radius: 26px; overflow: hidden;
  }
  .card--front { top: 175px; background: var(--paper); }
  .card--back { top: 685px; background: var(--gold); }

  .wave { position: absolute; inset: 0; width: 100%; height: 100%; }

  .holder { position: absolute; left: 46px; top: 60px; }
  .holder__name {
    font-weight: 700; font-size: 23px; letter-spacing: 0.2px; color: var(--navy);
  }
  .holder__name span { color: var(--gold); }
  .holder__role { font-size: 20px; color: var(--ink); margin-top: 4px; }

  .brand {
    position: absolute; display: flex; align-items: center; gap: 12px;
    font-weight: 700; white-space: nowrap;
  }
  .brand__dot { border-radius: 50%; flex: none; }
  .card--front .brand { right: 52px; top: 78px; font-size: 34px; color: var(--navy); }
  .card--front .brand__dot { width: 22px; height: 22px; background: var(--gold); }
  .card--back .brand {
    left: 50%; top: 50%; transform: translate(-50%, -50%);
    font-size: 58px; color: var(--paper);
  }
  .card--back .brand__dot { width: 38px; height: 38px; background: var(--paper); }

  .contact { position: absolute; left: 44px; top: 234px; list-style: none; }
  .contact li {
    display: flex; align-items: center; gap: 11px;
    height: 32px; font-size: 20px; color: var(--ink);
  }
  .contact svg { width: 22px; height: 18px; flex: none; fill: var(--gold); }

  .address {
    position: absolute; right: 44px; top: 264px;
    font-size: 20px; line-height: 29px; text-align: right; color: var(--ink);
  }
</style>
</head>
<body>

<section class="card card--front">
  <svg class="wave" viewBox="0 0 1317 746" preserveAspectRatio="none" aria-hidden="true">
    <path fill="var(--gold)" d="M0,485 C160,610 300,660 520,652 C780,640 1000,560 1317,662 L1317,746 L0,746 Z"/>
    <path fill="var(--navy)" d="M155,579 C300,648 500,645 720,612 C920,582 1060,560 1212,614 C1060,586 920,594 720,626 C500,660 300,656 155,579 Z"/>
  </svg>

  <div class="holder">
    <p class="holder__name">DANA <span>WHITFIELD</span></p>
    <p class="holder__role">Owner</p>
  </div>

  <div class="brand"><span class="brand__dot"></span>Heron Loan Partners</div>

  <ul class="contact">
    <li>
      <svg viewBox="0 0 22 18" aria-hidden="true"><path d="M1,6 C1,2 5,1 11,1 C17,1 21,2 21,6 L16,7 L15,4 L7,4 L6,7 Z M5,8 L17,8 L20,17 L2,17 Z"/></svg>
      555.014.2290
    </li>
    <li>
      <svg viewBox="0 0 22 18" aria-hidden="true"><path d="M1,2 L21,2 L11,10 Z M1,4 L11,12 L21,4 L21,16 L1,16 Z"/></svg>
      info@heronloanpartners.com
    </li>
    <li>
      <svg viewBox="0 0 22 18" aria-hidden="true"><circle cx="11" cy="9" r="8.5"/></svg>
      www.heronloanpartners.com
    </li>
  </ul>

  <p class="address">480 Elm Crest Ave, Ste<br>200, Fairview, TX 75069</p>
</section>

<section class="card card--back">
  <div class="brand"><span class="brand__dot"></span>Heron Loan Partners</div>
</section>

</body>
</html>
```